BildeVOLD buisnesscard

Hey :) I need a modern buisnesscard for my company BildeVOLD
It most have:
Dagligleder og Fotograf: Henrik Audun Strandvik

Mob: +00 000 00 000
Epost: post@bildevold.example
Adresse: Kvernbakken9, 0000 Fjordheimsby

Facbook and instagram logo with text BildeVOLD

BildeVOLD logo

It Company

```html
<!DOCTYPE html>
<html lang="no">
<head>
<meta charset="utf-8">
<title>BildeVOLD – visittkort</title>
<link href="https://fonts.googleapis.com/css2?family=Jost:wght@400;500;600&display=swap" rel="stylesheet">
<style>
  :root {
    --backdrop: #3a3a3a;
    --card-dark: #222223;
    --card-dark-soft: #29292a;
    --brand-blue: #1f77a6;
    --brand-blue-bright: #2a8ec4;
    --brand-pink: #d2408f;
    --social-blue: #3a57a8;
    --text-light: #ffffff;
  }
  html, body {
    margin: 0;
    width: 1200px;
    height: 799px;
    overflow: hidden;
    background: var(--backdrop);
    font-family: "Jost", "Futura", sans-serif;
  }
  .stage {
    position: relative;
    width: 1200px;
    height: 799px;
  }
  .card {
    position: absolute;
    top: 90px;
    width: 380px;
    height: 620px;
    background: var(--card-dark);
    overflow: hidden;
    box-shadow: 0 10px 30px rgba(0,0,0,.45);
  }
  .card--front { left: 190px; }
  .card--back  { left: 630px; }

  .card__bands {
    position: absolute;
    inset: 0;
  }
  .brand-name {
    position: absolute;
    left: 0;
    right: 0;
    margin: 0;
    text-align: center;
    color: var(--brand-blue-bright);
    font-weight: 600;
    letter-spacing: .5px;
  }
  .card--front .brand-name { top: 112px; font-size: 42px; }

  .person {
    position: absolute;
    top: 192px;
    left: 0;
    right: 0;
    text-align: center;
  }
  .person__name {
    margin: 0;
    color: var(--brand-blue-bright);
    font-size: 22px;
    font-weight: 500;
    letter-spacing: .4px;
  }
  .person__role {
    margin: 4px 0 0;
    color: var(--brand-pink);
    font-size: 16px;
    font-weight: 400;
  }

  .contact {
    position: absolute;
    left: 34px;
    bottom: 34px;
    color: var(--text-light);
    font-size: 17px;
    font-style: normal;
    line-height: 1.35;
  }
  .contact__address { margin: 0 0 12px; }
  .contact__list { list-style: none; margin: 0; padding: 0; }
  .contact__item { display: flex; align-items: center; gap: 10px; }
  .contact__icon { width: 16px; height: 16px; flex: none; }

  .card--back .brand-name { top: 232px; font-size: 48px; }
  .social {
    position: absolute;
    top: 310px;
    left: 0;
    right: 0;
    display: flex;
    justify-content: center;
    gap: 8px;
  }
  .social__dot { width: 26px; height: 26px; border-radius: 50%; }
  .social__dot--blue { background: var(--social-blue); }
  .social__dot--pink { background: var(--brand-pink); }
  .back-rule {
    position: absolute;
    top: 350px;
    left: 90px;
    width: 200px;
    height: 1px;
    background: linear-gradient(90deg, transparent, #bbb 50%, transparent);
  }
</style>
</head>
<body>
<main class="stage">

  <section class="card card--front" aria-label="Forside">
    <svg class="card__bands" viewBox="0 0 380 620" width="380" height="620" aria-hidden="true">
      <polygon points="0,340 380,445 380,620 0,620" fill="var(--brand-pink)"/>
      <polygon points="0,354 380,459 380,620 0,620" fill="var(--brand-blue)"/>
    </svg>
    <h1 class="brand-name">BildeVOLD</h1>
    <div class="person">
      <p class="person__name">Henrik Audun Strandvik</p>
      <p class="person__role">Dagligleder og Fotograf</p>
    </div>
    <address class="contact">
      <p class="contact__address">Kvernbakken9<br>0000 Fjordheimsby</p>
      <ul class="contact__list">
        <li class="contact__item">
          <svg class="contact__icon" viewBox="0 0 16 16" aria-hidden="true"><rect x="4" y="1" width="8" height="14" rx="1.5" fill="none" stroke="#fff" stroke-width="1.4"/><line x1="7" y1="12.5" x2="9" y2="12.5" stroke="#fff" stroke-width="1.2"/></svg>
          +00 000 00 000
        </li>
        <li class="contact__item">
          <svg class="contact__icon" viewBox="0 0 16 16" aria-hidden="true"><rect x="1" y="3" width="14" height="10" fill="#fff"/><polyline points="1,3 8,9 15,3" fill="none" stroke="var(--brand-blue)" stroke-width="1.2"/></svg>
          post@bildevold.example
        </li>
        <li class="contact__item">
          <svg class="contact__icon" viewBox="0 0 16 16" aria-hidden="true"><circle cx="8" cy="8" r="7" fill="#fff"/><ellipse cx="8" cy="8" rx="3" ry="7" fill="none" stroke="var(--brand-blue)" stroke-width="1"/><line x1="1" y1="8" x2="15" y2="8" stroke="var(--brand-blue)" stroke-width="1"/></svg>
          www.bildevold.example
        </li>
      </ul>
    </address>
  </section>

  <section class="card card--back" aria-label="Bakside">
    <svg class="card__bands" viewBox="0 0 380 620" width="380" height="620" aria-hidden="true">
      <polygon points="0,430 380,540 380,620 0,620" fill="var(--card-dark-soft)"/>
    </svg>
    <h2 class="brand-name">BildeVOLD</h2>
    <div class="social" aria-label="Sosiale medier">
      <span class="social__dot social__dot--blue"></span>
      <span class="social__dot social__dot--pink"></span>
    </div>
    <div class="back-rule"></div>
  </section>

</main>
</body>
</html>
```